Kovát Lillas Physiotherapy Business Card Vienna

We need a business card design for a newly created Physiotherapy company based in Vienna Austria.
We seek a simple, modern, minimalist design without too much color variation. The font should look young/fresh, but definitely not childish or so. Since we are a starting Business, we currently haven't got a logo, if you feel like a logo would fit your design, feel free to use one, but it's not necessary.
Target Market(s)
Healthcare, young and elderly people with mobility issues
Industry/Entity Type
Health And Wellness
Contact Information for Business Card
Name: Lilla Kovát
Title description: Physiotherapist
Phone num: +43 664 2951 4086
e-mail: lilla.praxis@bluemail.example
Colors
Designer to choose colors to be used in the design.
Requirements
Must have
- Final design language must be in German, basically, the Title Description needs to be "Physiotherapeutin" the other details remain as in the English Language.
Nice to have
- Simple, modern, minimalist design
Should not have
- too many colors, Obvious use of a skeleton, skull, spline

```html
<!DOCTYPE html>
<html lang="de">
<head>
<meta charset="utf-8">
<title>Lilla Kovát – Physiotherapeutin – Visitenkarte</title>
<link rel="stylesheet" href="https://fonts.googleapis.com/css2?family=Josefin+Sans:wght@300;400;600&family=Montserrat:wght@400&display=swap">
<style>
  :root {
    --page: #ffffff;
    --card-dark: #1b1b1d;
    --card-light: #f1f1f1;
    --ink-light: #f4f4f4;
    --ink-dark: #1a1a1a;
    --mark-grey: #6a6a6a;
    --rule: #555555;
  }
  * { margin: 0; padding: 0; box-sizing: border-box; }
  html, body {
    width: 1200px; height: 1200px; overflow: hidden;
    background: var(--page);
  }
  .canvas { position: relative; width: 1200px; height: 1200px; }

  .card { position: absolute; width: 720px; height: 412px; }

  /* Front */
  .card-front {
    left: 250px; top: 103px;
    background: var(--card-dark);
    overflow: hidden;
  }
  .front-corner { position: absolute; left: 0; top: 0; width: 720px; height: 412px; }
  .front-wordmark {
    position: absolute; left: 0; right: 0; top: 108px;
    text-align: center;
    font-family: "Josefin Sans", sans-serif;
    font-weight: 600; font-size: 24px; letter-spacing: 1px;
    color: var(--mark-grey);
  }
  .front-name {
    position: absolute; left: 0; right: 0; top: 186px;
    text-align: center;
    font-family: "Josefin Sans", sans-serif;
    font-weight: 600; font-size: 56px; font-variant: small-caps;
    letter-spacing: 1px; color: var(--ink-light); line-height: 1;
  }
  .front-title {
    position: absolute; left: 0; right: 0; top: 247px;
    text-align: center;
    font-family: "Josefin Sans", sans-serif;
    font-weight: 300; font-size: 30px; font-variant: small-caps;
    color: var(--ink-light); line-height: 1;
  }

  /* Back */
  .card-back {
    left: 253px; top: 637px;
    background: var(--card-dark);
  }
  .back-panel {
    position: absolute; left: 13px; top: 13px; right: 13px; bottom: 13px;
    background: var(--card-light);
    border-radius: 10px;
    overflow: hidden;
    box-shadow: inset 0 0 6px rgba(0,0,0,0.55), 0 0 3px rgba(255,255,255,0.5);
  }
  .back-name {
    position: absolute; left: 44px; top: 104px;
    font-family: "Josefin Sans", sans-serif;
    font-weight: 600; font-size: 42px; font-variant: small-caps;
    letter-spacing: 0.5px; color: var(--ink-dark); line-height: 1;
  }
  .back-title {
    position: absolute; left: 44px; top: 143px;
    font-family: "Josefin Sans", sans-serif;
    font-weight: 300; font-size: 30px; font-variant: small-caps;
    color: var(--ink-dark); line-height: 1;
  }
  .back-rule {
    position: absolute; left: 44px; top: 191px;
    width: 236px; height: 1px; background: var(--rule);
  }
  .back-contact {
    position: absolute; left: 55px; top: 226px;
    list-style: none;
    font-family: "Montserrat", sans-serif;
    font-weight: 400; font-size: 17.5px; color: var(--ink-dark);
    line-height: 33px;
  }
  .back-wordmark {
    position: absolute; left: 330px; top: 64px; width: 340px; height: 210px;
    display: flex; flex-direction: column; justify-content: center; align-items: flex-end;
    font-family: "Josefin Sans", sans-serif;
    font-weight: 600; font-size: 40px; line-height: 1.15;
    color: var(--ink-dark); text-align: right; white-space: nowrap;
  }
</style>
</head>
<body>
<main class="canvas">

  <section class="card card-front" aria-label="Vorderseite">
    <svg class="front-corner" viewBox="0 0 720 412" aria-hidden="true">
      <polygon points="0,295 120,412 0,412" fill="#f1f1f1"/>
      <line x1="0" y1="295" x2="120" y2="412" stroke="#8a8a8a" stroke-width="2"/>
    </svg>
    <p class="front-wordmark">Kovát Lillas Physiotherapy</p>
    <h1 class="front-name">Lilla Kovát</h1>
    <p class="front-title">Physiotherapeutin</p>
  </section>

  <section class="card card-back" aria-label="Rückseite">
    <div class="back-panel">
      <h2 class="back-name">Lilla Kovát</h2>
      <p class="back-title">Physiotherapeutin</p>
      <div class="back-rule"></div>
      <ul class="back-contact">
        <li>+43 664 2951 4086</li>
        <li>lilla.praxis@bluemail.example</li>
      </ul>
      <p class="back-wordmark"><span>Kovát Lillas</span><span>Physiotherapy</span></p>
    </div>
  </section>

</main>
</body>
</html>
```